Business Name: K&M Group Cleaning Services - Cleaning business

We need a website to be able to get our services out to the market..
We have just invested over $60,000 in our new van which is capable of doing specialised cleaning services see attached flyer... I will also send through our company logo....We do all types of cleaning from move out cleans, office cleans and have the capability fire flood and restoration services as well
On the flyer it has Desmond as a contact do not use his name only use Glenn as a contact
Want some good pictures included
Prefer people to contact me via email rather than calling me.

```html
<!DOCTYPE html>
<html lang="en">
<head>
<meta charset="utf-8">
<title>K&amp;M Group Cleaning Services</title>
<link href="https://fonts.googleapis.com/css2?family=Montserrat:wght@400;500;600;700&family=Open+Sans:wght@400;600;700&display=swap" rel="stylesheet">
<style>
:root{
  --orange:#f26b1d;
  --orange-dark:#d9560c;
  --ink:#222222;
  --text:#6b6b6b;
  --light:#f5f5f5;
  --ghost:#ececec;
  --footer:#1b1b1b;
  --white:#ffffff;
}
*{box-sizing:border-box;margin:0;padding:0}
html,body{width:1200px;height:4306px;overflow:hidden}
body{position:relative;background:var(--white);font-family:"Open Sans",sans-serif;color:var(--text)}
.abs{position:absolute}
.heading{font-family:"Montserrat",sans-serif;color:var(--ink);font-weight:600;letter-spacing:1px}
.ghost{font-family:"Montserrat",sans-serif;font-weight:600;color:var(--ghost);letter-spacing:4px;white-space:nowrap}
.center{left:0;width:1200px;text-align:center}
.btn{display:inline-block;background:var(--orange);color:var(--white);font-family:"Montserrat",sans-serif;font-weight:600;font-size:16px;border-radius:30px;text-align:center}
.btn-outline{background:var(--white);color:var(--orange);border:2px solid #f3c7ad}
.arrow-dot{display:inline-block;width:14px;height:14px;border-radius:50%;background:currentColor;vertical-align:-2px;margin-left:6px}

/* top bar */
.topbar{top:0;left:600px;width:600px;height:38px;background:var(--orange);clip-path:polygon(40px 0,100% 0,100% 100%,0 100%);color:var(--white);font-size:15px;display:flex;align-items:center;gap:24px;padding-left:56px}
.nav{top:88px;right:112px;display:flex;gap:24px;font-family:"Montserrat",sans-serif;font-weight:600;font-size:16px;color:var(--ink)}
.nav .active{color:var(--orange)}
.nav-search{top:88px;right:56px;width:20px;height:20px}
.brand-badge{top:20px;left:110px;width:200px;height:200px;border-radius:50%;background:var(--white);z-index:3;text-align:center;padding-top:118px}
.brand-badge .mark{position:absolute;top:22px;left:66px;width:68px;height:68px;border-radius:50%;border:4px solid var(--orange)}
.brand-name{font-family:"Montserrat",sans-serif;font-weight:600;font-size:27px;color:var(--ink);letter-spacing:1px}
.brand-sub{font-family:"Montserrat",sans-serif;font-weight:600;font-size:13px;color:var(--ink);letter-spacing:3px}

/* hero */
.hero{top:165px;left:0;width:1200px;height:620px;background:linear-gradient(100deg,#4a4a48 0%,#6f7478 35%,#8aa0a8 60%,#9aa39a 80%,#5e6b4c 100%)}
.hero-title{top:340px;left:110px;font-family:"Montserrat",sans-serif;font-weight:600;font-size:50px;color:var(--white);letter-spacing:1px}
.hero-text{top:412px;left:112px;width:520px;font-size:19px;line-height:28px;color:var(--white);font-weight:600}
.hero-btn{top:500px;left:112px;width:184px;height:46px;line-height:46px}
.hero-arrow{top:415px;width:20px;height:20px;color:var(--white);font-size:22px}
.hero-wave{top:640px;left:0;width:1200px;height:160px}

/* services */
.svc-ghost{top:870px;font-size:88px}
.svc-title{top:905px;font-size:44px}
.svc-sub{top:990px;left:230px;width:740px;text-align:center;font-size:14px;line-height:27px}
.svc{width:160px;text-align:center;top:1065px}
.svc-icon{width:130px;height:130px;margin:0 auto;border-radius:0 0 65px 65px;border-bottom:5px solid var(--orange);background:linear-gradient(#fff,#fde6d8);display:flex;align-items:center;justify-content:center}
.svc-name{font-family:"Montserrat",sans-serif;font-weight:600;font-size:20px;color:var(--ink);margin-top:20px;white-space:nowrap}
.svc-text{font-size:13px;line-height:23px;margin-top:10px}
.circle-arrow{width:48px;height:48px;border-radius:50%;display:flex;align-items:center;justify-content:center}
.ca-solid{background:var(--orange)}
.ca-outline{background:var(--white);border:2px solid #f3c7ad}

/* about */
.about-ghost{top:1375px;left:1188px;font-size:88px;transform:rotate(90deg);transform-origin:left top;color:#eeeeee}
.about-title{top:1540px;left:112px;font-size:44px}
.about-p{left:112px;width:460px;font-size:15px;line-height:27px}
.about-btn{top:1825px;left:112px;width:178px;height:46px;line-height:42px}
.about-photo{top:1515px;left:655px;width:400px;height:400px;border-radius:50%;border:8px solid #eee;background:radial-gradient(circle at 60% 45%,#b9b7a8,#6f7a80 60%,#3d4752);overflow:hidden}
.play{top:1680px;left:822px;width:66px;height:66px;border-radius:50%;background:var(--orange);border:5px solid rgba(255,255,255,.7)}

/* clients */
.clients{top:1970px;left:0;width:1200px;height:640px}
.clients-title{top:2160px;font-size:42px;color:var(--white)}
.tcard{top:2275px;width:302px;height:205px;background:var(--white);box-shadow:0 4px 14px rgba(0,0,0,.12);text-align:center;padding:14px 22px 0}
.quote{font-family:"Montserrat",sans-serif;font-size:64px;line-height:48px;color:#cfcfcf;height:40px}
.tcard p{font-size:12.5px;line-height:21px}
.avatar{top:2442px;width:82px;height:82px;border-radius:50%;background:linear-gradient(#c8c3bb,#8b8f96);border:4px solid var(--white)}
.tname{top:2534px;width:360px;text-align:center;font-size:15px;color:var(--ink)}
.tname b{font-family:"Montserrat",sans-serif}

/* works */
.divider{top:2675px;left:112px;width:976px;height:1px;background:#dcdcdc}
.works-ghost{top:2705px;font-size:80px}
.works-title{top:2752px;font-size:44px}
.works-sub{top:2828px;left:200px;width:800px;text-align:center;font-size:15px;line-height:28px}
.work{top:2913px;height:196px;width:236px}

/* blog */
.blog-ghost{top:3195px;font-size:80px}
.blog-title{top:3235px;font-size:44px}
.blog-sub{top:3305px;left:300px;width:600px;text-align:center;font-size:14px;line-height:26px}
.post{top:3395px;width:473px;height:210px;background:var(--white);box-shadow:0 4px 14px rgba(0,0,0,.1);display:flex}
.post-img{width:188px;height:210px}
.post-body{padding:20px 18px;flex:1}
.post-title{font-family:"Montserrat",sans-serif;font-weight:600;font-size:21px;color:var(--ink)}
.post-date{color:var(--orange);font-size:12px;margin:6px 0 10px}
.post-body p{font-size:13px;line-height:22px}
.post-meta{display:flex;justify-content:space-between;margin-top:12px;font-size:12px}
.post-meta .more{color:var(--orange);font-weight:700;font-family:"Montserrat",sans-serif}
.blog-btn{top:3665px;left:500px;width:200px;height:46px;line-height:46px}

/* footer */
.footer-wave{top:3770px;left:0;width:1200px;height:160px}
.footer{top:3915px;left:0;width:1200px;height:391px;background:var(--footer);color:#dcdcdc}
.f-mark{top:3960px;left:140px;width:76px;height:76px;border-radius:50%;border:4px solid var(--white)}
.f-brand{top:4055px;left:100px;width:160px;text-align:center;color:var(--white)}
.f-brand .brand-name,.f-brand .brand-sub{color:var(--white)}
.f-head{font-family:"Montserrat",sans-serif;font-weight:700;font-size:16px;color:var(--white)}
.f-row{display:flex;gap:20px;font-size:14px;line-height:22px;margin-top:20px;color:#e0e0e0}
.f-row svg{flex:none;margin-top:2px}
.news-input{width:202px;height:34px;border:1px solid #aaa;color:#ddd;font-size:12px;padding:8px 10px;margin-top:16px}
.news-btn{width:108px;height:36px;line-height:36px;font-size:12px;margin-top:18px}
.socials{top:4186px;left:510px;display:flex;gap:14px}
.socials span{width:40px;height:40px;border-radius:50%;border:2px solid #bbb;display:block}
.f-line{top:4240px;left:112px;width:976px;height:1px;background:#444}
.copy{top:4256px;font-size:14px;color:#ddd}
</style>
</head>
<body>

<!-- Header -->
<div class="abs topbar">
  <span>&#9742; 0491 570 156</span><span>|</span><span>&#9993; kmgroup.cleaning@mailbox.example</span>
</div>
<nav class="abs nav">
  <span class="active">HOME</span><span>ABOUT US</span><span>SERVICES</span><span>BLOG</span><span>GALLERY</span><span>CONTACT US</span>
</nav>
<svg class="abs nav-search" viewBox="0 0 20 20"><circle cx="8" cy="8" r="6" fill="none" stroke="#222" stroke-width="2.5"/><line x1="12.5" y1="12.5" x2="18" y2="18" stroke="#222" stroke-width="2.5"/></svg>

<div class="abs brand-badge">
  <span class="mark"></span>
  <div class="brand-name">K&amp;M GROUP</div>
  <div class="brand-sub">CLEANING</div>
</div>

<!-- Hero -->
<div class="abs hero" role="img" aria-label="Worker pressure cleaning a stone patio beside a brick wall"></div>
<div class="abs hero-title">PRESSURE CLEAN</div>
<div class="abs hero-text">Our professional Onyx 500 Truckmount unit, is one of the most powerful slide-in on the market...</div>
<div class="abs btn hero-btn">READ MORE<span class="arrow-dot"></span></div>
<div class="abs hero-arrow" style="left:40px">&#8249;</div>
<div class="abs hero-arrow" style="left:1142px">&#8250;</div>
<svg class="abs hero-wave" viewBox="0 0 1200 160" preserveAspectRatio="none">
  <path d="M0 40 Q600 170 1200 40 L1200 160 L0 160Z" fill="#fff"/>
  <path d="M0 40 Q600 170 1200 40" fill="none" stroke="#f26b1d" stroke-width="7"/>
  <rect x="588" y="22" width="24" height="38" rx="12" fill="none" stroke="#fff" stroke-width="2.5"/>
  <line x1="600" y1="30" x2="600" y2="40" stroke="#fff" stroke-width="2.5"/>
  <line x1="600" y1="62" x2="600" y2="78" stroke="#fff" stroke-width="2"/>
</svg>

<!-- Services -->
<div class="abs ghost center svc-ghost">OUR SERVICES</div>
<h2 class="abs heading center svc-title">WE SPECIALISE IN</h2>
<p class="abs svc-sub">The Onyx Truckmount has the Ability to steam clean at higher temperatures thus provides quality results &amp; higher sanitisation rates than normal portable steam or pressure cleaners.</p>

<div class="abs circle-arrow ca-solid" style="top:1195px;left:28px"><svg width="14" height="14" viewBox="0 0 14 14"><path d="M9 2 L4 7 L9 12" fill="none" stroke="#fff" stroke-width="2.5"/></svg></div>
<div class="abs circle-arrow ca-outline" style="top:1195px;left:1122px"><svg width="14" height="14" viewBox="0 0 14 14"><path d="M5 2 L10 7 L5 12" fill="none" stroke="#f26b1d" stroke-width="2.5"/></svg></div>

<div class="abs svc" style="left:104px">
  <div class="svc-icon"><svg width="64" height="64" viewBox="0 0 64 64" fill="none" stroke="#222" stroke-width="3" stroke-linecap="round"><rect x="8" y="34" width="22" height="20" rx="3"/><path d="M19 34 V22 H40 L48 14"/><path d="M52 10 l6 -4 M53 16 h7 M52 22 l6 4" stroke="#f26b1d"/></svg></div>
  <div class="svc-name">Pressure Clean</div><p class="svc-text">Lorem ipsum dolor sit amet consectetur adipiscing elit, sed do eiusmod tempor incidi.</p>
</div>
<div class="abs svc" style="left:270px">
  <div class="svc-icon"><svg width="64" height="64" viewBox="0 0 64 64" fill="none" stroke="#222" stroke-width="3"><rect x="10" y="10" width="44" height="44"/><path d="M32 10 V54 M10 32 H54"/><path d="M16 16 l10 10" stroke="#f26b1d" stroke-linecap="round"/></svg></div>
  <div class="svc-name">Tile &amp; Grout</div><p class="svc-text">Lorem ipsum dolor sit amet consectetur adipiscing elit, sed do eiusmod tempor incidi.</p>
</div>
<div class="abs svc" style="left:436px">
  <div class="svc-icon"><svg width="64" height="64" viewBox="0 0 64 64" fill="none" stroke="#222" stroke-width="3" stroke-linecap="round"><path d="M6 18 H58 L52 30 H12 Z"/><path d="M46 30 V48"/><path d="M22 42 v4 M32 38 v4" stroke="#f26b1d"/></svg></div>
  <div class="svc-name">Gutter Cleaning</div><p class="svc-text">Lorem ipsum dolor sit amet consectetur adipiscing elit, sed do eiusmod tempor incidi.</p>
</div>
<div class="abs svc" style="left:602px">
  <div class="svc-icon"><svg width="64" height="64" viewBox="0 0 64 64" fill="none" stroke-width="3" stroke-linecap="round"><path d="M32 8 C40 18 44 24 44 32 A12 12 0 0 1 20 32 C20 24 26 20 32 8Z" stroke="#f26b1d"/><path d="M6 50 q6 -6 13 0 t13 0 t13 0 t13 0" stroke="#222"/></svg></div>
  <div class="svc-name">Fire &amp; flood</div><p class="svc-text">Lorem ipsum dolor sit amet consectetur adipiscing elit, sed do eiusmod tempor incidi.</p>
</div>
<div class="abs svc" style="left:768px">
  <div class="svc-icon"><svg width="64" height="64" viewBox="0 0 64 64" fill="none" stroke="#222" stroke-width="3" stroke-linejoin="round"><path d="M10 22 L32 12 L54 22 V48 L32 58 L10 48 Z"/><path d="M10 22 L32 32 L54 22 M32 32 V58"/><path d="M21 17 L43 27" stroke="#f26b1d"/></svg></div>
  <div class="svc-name">Move Out Cleans</div><p class="svc-text">Lorem ipsum dolor sit amet consectetur adipiscing elit, sed do eiusmod tempor incidi.</p>
</div>
<div class="abs svc" style="left:934px">
  <div class="svc-icon"><svg width="64" height="64" viewBox="0 0 64 64" fill="none" stroke="#222" stroke-width="3"><rect x="14" y="8" width="36" height="48"/><path d="M22 18 h6 M36 18 h6 M22 28 h6 M36 28 h6 M22 38 h6 M36 38 h6"/><path d="M28 56 V46 H36 V56" stroke="#f26b1d"/></svg></div>
  <div class="svc-name">Office Cleans</div><p class="svc-text">Lorem ipsum dolor sit amet consectetur adipiscing elit, sed do eiusmod tempor incidi.</p>
</div>

<!-- About -->
<div class="abs ghost about-ghost">ABOUT US</div>
<h2 class="abs heading about-title">ABOUT K&amp;M GROUP</h2>
<p class="abs about-p" style="top:1620px">Lorem ipsum dolor sit amet, consectetur adipiscing elit, sed do eiusmod tempor incididunt ut labore et dolore magna aliqua.</p>
<p class="abs about-p" style="top:1695px">Ut enim ad minim veniam, quis nostrud exercitation ullamco laboris nisi ut aliquip ex ea commodo consequat. Duis aute irure dolor in reprehenderit in voluptate velit esse cillum dolore eu fugiat nulla pariatur. Excepteur sint occaecat cupidatat...</p>
<div class="abs btn btn-outline about-btn">READ MORE<span class="arrow-dot"></span></div>
<div class="abs about-photo" role="img" aria-label="Worker in boots pressure cleaning a wet driveway"></div>
<div class="abs play"><svg width="56" height="56" viewBox="0 0 56 56"><path d="M22 17 L38 28 L22 39Z" fill="#fff"/></svg></div>

<!-- Clients -->
<svg class="abs clients" viewBox="0 0 1200 640" preserveAspectRatio="none">
  <path d="M0 60 Q600 -50 1200 60 L1200 305 L0 305Z" fill="#f26b1d"/>
  <rect x="0" y="305" width="1200" height="315" fill="#f5f5f5"/>
</svg>
<h2 class="abs heading center clients-title">WHAT OUR CLIENTS SAY</h2>
<div class="abs circle-arrow ca-solid" style="top:2352px;left:28px;border:2px solid #fff"><svg width="14" height="14" viewBox="0 0 14 14"><path d="M9 2 L4 7 L9 12" fill="none" stroke="#fff" stroke-width="2.5"/></svg></div>
<div class="abs circle-arrow ca-outline" style="top:2352px;left:1122px"><svg width="14" height="14" viewBox="0 0 14 14"><path d="M5 2 L10 7 L5 12" fill="none" stroke="#f26b1d" stroke-width="2.5"/></svg></div>

<div class="abs tcard" style="left:112px"><div class="quote">&ldquo;</div><p>"At vero eos et accusamus et iusto odio dignissimos ducimus qui blanditiis tatum deligit enitt atque corrupti quos dolores et quas ex fite gitr molestias"</p></div>
<div class="abs tcard" style="left:449px"><div class="quote">&ldquo;</div><p>"At vero eos et accusamus et iusto odio dignissimos ducimus qui blanditiis tatum deligit enitt atque corrupti quos dolores et quas ex fite gitr molestias"</p></div>
<div class="abs tcard" style="left:788px"><div class="quote">&ldquo;</div><p>"At vero eos et accusamus et iusto odio dignissimos ducimus qui blanditiis tatum deligit enitt atque corrupti quos dolores et quas ex fite gitr molestias"</p></div>

<div class="abs avatar" style="left:222px" role="img" aria-label="Client portrait"></div>
<div class="abs avatar" style="left:559px" role="img" aria-label="Client portrait"></div>
<div class="abs avatar" style="left:898px" role="img" aria-label="Client portrait"></div>
<div class="abs tname" style="left:83px"><b>PRIYA NAIR,</b> Creative Manager</div>
<div class="abs tname" style="left:420px"><b>MARA ELLIS,</b> Creative Manager</div>
<div class="abs tname" style="left:759px"><b>LEON BROOKS,</b> Creative Manager</div>

<!-- Works -->
<div class="abs divider"></div>
<div class="abs ghost center works-ghost">OUR WORKS</div>
<h2 class="abs heading center works-title">OUR WORKS</h2>
<p class="abs works-sub">Lorem ipsum dolor sit amet, consectetur adipiscing elit, sed do eiusmod tempor incididunt ut labore et dolore magna aliqua. Ut enim ad minim veniam, quis nostrud exercitation ullamco laboris nisi ut aliquip.</p>
<div class="abs work" style="left:0;background:linear-gradient(135deg,#5c6a3e,#9fa07c,#7b6c55)" role="img" aria-label="Pressure cleaning a garden path"></div>
<div class="abs work" style="left:241px;background:linear-gradient(135deg,#8d8a7e,#c9c4b4,#6e6d64)" role="img" aria-label="Worker cleaning a paved surface"></div>
<div class="abs work" style="left:482px;background:linear-gradient(135deg,#a9a49a,#d8d4cb,#6b7079)" role="img" aria-label="Worker with pressure washer on concrete"></div>
<div class="abs work" style="left:723px;background:linear-gradient(135deg,#b85d34,#d98a55,#8a6f5a)" role="img" aria-label="Cleaning a building facade from a lift"></div>
<div class="abs work" style="left:964px;width:236px;background:linear-gradient(135deg,#7a9bb5,#9b4d36,#6b7c52)" role="img" aria-label="Roof tiles being pressure cleaned"></div>

<!-- Blog -->
<div class="abs ghost center blog-ghost">LATEST BLOG POST</div>
<h2 class="abs heading center blog-title">LATEST BLOG POST</h2>
<p class="abs blog-sub">Lorem ipsum dolor sit amet, consectetur adipiscing elit, sed do eiusmod tempor incididunt ut exercitation ullamco laboris nisi ut labore et dolore magna aliqua.</p>

<div class="abs post" style="left:110px">
  <div class="post-img" role="img" aria-label="Worker with a hose reel pressure cleaning" style="background:linear-gradient(135deg,#b06a3a,#d9c6a8,#6d6a5c)"></div>
  <div class="post-body">
    <div class="post-title">IPSAM VOLUPTATEM</div>
    <div class="post-date">&#9632; MAR 12, 2019</div>
    <p>At vero eos et accusam moset iusto odio dignissimos ducimus qui prae seum tre voluptatum...</p>
    <div class="post-meta"><span class="more">READ MORE</span><span>20 comments</span></div>
  </div>
</div>
<div class="abs post" style="left:617px">
  <div class="post-img" role="img" aria-label="Worker in protective gear cleaning a floor" style="background:linear-gradient(135deg,#6c7480,#c15a2c,#8d8a86)"></div>
  <div class="post-body">
    <div class="post-title">ACCUSAMUS ET IUSTO</div>
    <div class="post-date">&#9632; MAR 12, 2019</div>
    <p>At vero eos et accusam moset iusto odio dignissimos ducimus qui prae seum tre voluptatum...</p>
    <div class="post-meta"><span class="more">READ MORE</span><span>20 comments</span></div>
  </div>
</div>
<div class="abs btn blog-btn">VIEW ALL BLOG<span class="arrow-dot"></span></div>

<!-- Footer -->
<svg class="abs footer-wave" viewBox="0 0 1200 160" preserveAspectRatio="none">
  <path d="M0 50 Q600 -40 1200 50 L1200 160 L0 160Z" fill="#f26b1d"/>
  <path d="M0 110 Q600 20 1200 110 L1200 160 L0 160Z" fill="#1b1b1b"/>
</svg>
<footer class="abs footer"></footer>
<div class="abs f-mark"></div>
<div class="abs f-brand"><div class="brand-name">K&amp;M GROUP</div><div class="brand-sub">CLEANING</div></div>

<div class="abs" style="top:3965px;left:410px;width:340px">
  <div class="f-head">CONTACT US</div>
  <div class="f-row"><svg width="14" height="18" viewBox="0 0 14 18"><path d="M7 0C3 0 0 3 0 7c0 5 7 11 7 11s7-6 7-11c0-4-3-7-7-7z" fill="#fff"/><circle cx="7" cy="7" r="2.5" fill="#1b1b1b"/></svg><span>K&amp;M Group, 27 Harbour Lane, Northvale 3099</span></div>
  <div class="f-row"><svg width="16" height="16" viewBox="0 0 16 16"><path d="M3 1l3 3-2 2c1 2 4 5 6 6l2-2 3 3-2 2C7 15 1 9 1 3z" fill="#fff"/></svg><span>0491 570 156</span></div>
  <div class="f-row"><svg width="16" height="12" viewBox="0 0 16 12"><rect width="16" height="12" fill="#fff"/><path d="M0 0l8 6 8-6" fill="none" stroke="#1b1b1b" stroke-width="1.5"/></svg><span>kmgroup.cleaning@mailbox.example</span></div>
</div>

<div class="abs" style="top:3965px;left:821px;width:280px">
  <div class="f-head">NEWSLETTER SUBSCRIPTION</div>
  <p style="font-size:14px;line-height:22px;margin-top:20px;color:#e0e0e0">Register your Email Address to get more information about us</p>
  <div class="news-input">Email Address</div>
  <div class="btn news-btn">SUBSCRIBE</div>
</div>

<div class="abs socials"><span></span><span></span><span></span><span></span></div>
<div class="abs f-line"></div>
<div class="abs center copy">Copyrights &copy; 2019 K&amp;M Group. All Rights Reserved &nbsp; | &nbsp; Privacy Policy.</div>

</body>
</html>
```